Design a large parking banner – mandatory ticket validation in the shop

Banner Size:
548 cm (width) x 154 cm (height)
Note: The banner will be placed in a metal frame at our parking lot entrance, fully visible to every incoming truck driver. The message must be easy to read from a distance.
Goal of the Banner:
To inform all truck drivers that they must validate their entry ticket inside the shop, even if they are parking for a short time.
The message must be displayed in multiple languages for international drivers.
Mandatory Content:
Main message – in multiple languages (clearly separated or stacked):
Dutch (NL): Vergeet je ticket niet te valideren in de shop – verplicht, ook bij kort parkeren!
French (FR): N'oubliez pas de valider votre ticket à la boutique – obligatoire, même pour un court arrêt !
English (EN): Don't forget to validate your entry ticket in the shop – mandatory, even for short stops!
German (DE): Vergessen Sie nicht, Ihr Einfahrticket im Shop zu entwerten – Pflicht, auch bei kurzem Parken!
Polish (PL): Nie zapomnij zatwierdzić biletu w sklepie – obowiązkowe, nawet przy krótkim postoju!
Romanian (RO): Nu uitați să validați biletul în magazin – obligatoriu, chiar și pentru opriri scurte!
You can include more languages if space allows, but these are essential.
Opening Hours Block (in one section below):
Shop Opening Hours
Mon – Fri: 05:30 – 22:00
Sat & Sun: 08:00 – 22:00
Style & Branding:
The design must match the visual identity of Haulport 41Ter
Please refer to the attached photos of existing parking signage for guidance on colors, typography, and layout style
Our logo (attached) must be clearly visible and professionally integrated
Feel free to use icons or pictograms to visually support the message (e.g., ticket, truck, arrow)
Readability is key – large, bold text and high contrast colors that are visible from a distance
Target Audience:
International truck drivers – people who need fast, clear communication. Not everyone speaks the local language, so visual clarity and multilingual messaging are critical.
File Requirements:
Print-ready file (PDF or EPS) – 300 dpi at 1:10 scale
Include 5 cm bleed on all sides
Provide open source files if possible (AI or PSD)

```html
<!DOCTYPE html>
<html lang="en">
<head>
<meta charset="utf-8">
<title>Haulport 41Ter – Ticket Validation Banner</title>
<link rel="stylesheet" href="https://fonts.googleapis.com/css2?family=Arimo:ital,wght@1,700&family=Archivo:ital,wght@1,800&display=swap">
<style>
  :root {
    --backdrop: #c9c9c9;
    --paper: #ffffff;
    --ink-navy: #1f2a5a;
    --label-red: #d4202a;
    --accent-blue: #1a7fc8;
    --band-navy: #1e2659;
    --arrow-blue-start: #1272bd;
    --arrow-blue-end: #2a9be0;
    --arrow-edge: #8fd0f5;
    --white: #ffffff;
  }
  * { box-sizing: border-box; margin: 0; padding: 0; }
  html, body { width: 1200px; height: 485px; overflow: hidden; }
  body { background: var(--backdrop); position: relative; font-family: "Arimo", Arial, sans-serif; }

  .banner {
    position: absolute; left: 62px; top: 90px;
    width: 1076px; height: 304px;
    background: var(--paper);
  }

  .messages { position: absolute; inset: 0 0 110px 0; }
  .message {
    position: absolute;
    font-style: italic; font-weight: 700;
    font-size: 15.2px; line-height: 20px;
    color: var(--ink-navy);
  }
  .message .lang { color: var(--label-red); }
  .message .note { color: var(--accent-blue); }

  .hours-band {
    position: absolute; left: 0; right: 0; bottom: 0; height: 110px;
    background: var(--band-navy);
  }
  .hours-arrow { position: absolute; left: 0; top: 0; }
  .hours-title {
    position: absolute; left: 25px; top: 24px;
    font-family: "Archivo", Arial, sans-serif; font-style: italic; font-weight: 800;
    font-size: 27px; line-height: 33px; color: var(--white); letter-spacing: 0.3px;
  }

  .schedule { position: absolute; top: 14px; }
  .schedule.weekdays { left: 327px; }
  .schedule.weekend { left: 568px; }
  .day-tag {
    position: relative; width: 235px; height: 42px;
    display: flex; align-items: center; gap: 8px; padding-left: 22px;
    font-family: "Archivo", Arial, sans-serif; font-style: italic; font-weight: 800;
    font-size: 29px; color: var(--white);
  }
  .day-tag::before {
    content: ""; position: absolute; inset: 0; z-index: 0;
    background: var(--label-red);
    clip-path: polygon(12px 0, 100% 0, calc(100% - 12px) 100%, 0 100%);
  }
  .day-tag > * { position: relative; z-index: 1; }
  .time-range {
    margin-top: 2px; padding-left: 4px;
    font-family: "Archivo", Arial, sans-serif; font-style: italic; font-weight: 800;
    font-size: 33px; line-height: 44px; color: var(--white);
  }

  .brand-name {
    position: absolute; left: 842px; top: 34px; width: 200px;
    font-family: "Archivo", Arial, sans-serif; font-style: italic; font-weight: 800;
    font-size: 28px; line-height: 40px; color: var(--white); text-align: center;
  }
</style>
</head>
<body>
  <div class="banner">
    <div class="messages">
      <p class="message" style="left:24px; top:21px; width:300px;"><span class="lang">Dutch (NL)</span> Vergeet je ticket niet te valideren in de shop – <span class="note">verplicht, ook bij kort parkeren!</span></p>
      <p class="message" style="left:26px; top:97px; width:290px;"><span class="lang">French (FR)</span>&nbsp; N'oubliez pas de valider votre ticket à la boutique – <span class="note">obligatoire, même pour un court arrêt !</span></p>

      <p class="message" style="left:340px; top:21px; width:360px;"><span class="lang">English (EN)</span> Don't forget to validate your entry ticket in the shop – <span class="note">mandatory, even for short stops!</span></p>
      <p class="message" style="left:340px; top:97px; width:360px;"><span class="lang">German (DE)</span> Vergessen Sie nicht, Ihr Einfahrticket im Shop zu entwerten – <span class="note">Pflicht, auch bei kurzem Parken!</span></p>

      <p class="message" style="left:718px; top:21px; width:300px;"><span class="lang">Polish (PL)</span> Nie zapomnij zatwierdzić biletu w sklepie – <span class="note">obowiązkowe, nawet przy</span></p>
      <p class="message" style="left:718px; top:97px; width:340px;"><span class="lang">Romanian (RO)</span> Nu uitați să validați biletul în magazin – <span class="note">obligatoriu, chiar și pentru opriri scurte!</span></p>
    </div>

    <div class="hours-band">
      <svg class="hours-arrow" width="290" height="110" viewBox="0 0 290 110" aria-hidden="true">
        <defs>
          <linearGradient id="arrowFill" x1="0" y1="1" x2="1" y2="0">
            <stop offset="0" stop-color="var(--arrow-blue-start)"/>
            <stop offset="1" stop-color="var(--arrow-blue-end)"/>
          </linearGradient>
        </defs>
        <polygon points="0,0 248,0 284,55 248,110 0,110" fill="url(#arrowFill)"/>
        <polyline points="248,0 284,55 248,110" fill="none" stroke="var(--arrow-edge)" stroke-width="3"/>
      </svg>
      <h2 class="hours-title">SHOP OPENING<br>HOURS</h2>

      <div class="schedule weekdays">
        <div class="day-tag">
          <svg width="26" height="24" viewBox="0 0 26 24" aria-hidden="true">
            <rect x="1.5" y="3.5" width="19" height="17" rx="2" fill="none" stroke="#fff" stroke-width="2.2"/>
            <rect x="1.5" y="3.5" width="19" height="5" fill="#fff"/>
            <rect x="5" y="0.5" width="2.5" height="5" fill="#fff"/><rect x="14.5" y="0.5" width="2.5" height="5" fill="#fff"/>
            <circle cx="19.5" cy="17.5" r="5.5" fill="var(--label-red)" stroke="#fff" stroke-width="2"/>
            <path d="M19.5 14.8v3h2" stroke="#fff" stroke-width="1.6" fill="none"/>
          </svg>
          <span>MON – FRI</span>
        </div>
        <p class="time-range">05:30 – 22:00</p>
      </div>

      <div class="schedule weekend">
        <div class="day-tag">
          <svg width="26" height="24" viewBox="0 0 26 24" aria-hidden="true">
            <rect x="1.5" y="3.5" width="19" height="17" rx="2" fill="none" stroke="#fff" stroke-width="2.2"/>
            <rect x="1.5" y="3.5" width="19" height="5" fill="#fff"/>
            <rect x="5" y="0.5" width="2.5" height="5" fill="#fff"/><rect x="14.5" y="0.5" width="2.5" height="5" fill="#fff"/>
            <circle cx="19.5" cy="17.5" r="5.5" fill="var(--label-red)" stroke="#fff" stroke-width="2"/>
            <path d="M19.5 14.8v3h2" stroke="#fff" stroke-width="1.6" fill="none"/>
          </svg>
          <span>SAT &amp; SUN</span>
        </div>
        <p class="time-range">08:00 – 22:00</p>
      </div>

      <p class="brand-name">Haulport 41Ter</p>
    </div>
  </div>
</body>
</html>
```